We need professional looking business cards for our e-assessment business based in Europe. Our company is called Velmo.

You can just use sample name and addresses.

The colours we use are:

#70abe4 (blue)
#FF6600 (orange)

The back side should say: Smart online assessments

This is the print-shop we are using. Please look at the link for info about formats: http://nl.prindavo.com/help/faq/using-my-own-artwork.html

Target market is education and large corporations

Business

```html
<!DOCTYPE html>
<html lang="en">
<head>
<meta charset="utf-8">
<title>Velmo business cards</title>
<link rel="stylesheet" href="https://fonts.googleapis.com/css2?family=Barlow:wght@400;500&display=swap">
<style>
  :root {
    --brand-orange: #ff6600;
    --mark-orange: #e85d0a;
    --brand-blue: #70abe4;
    --ink: #3a3a3a;
    --ink-soft: #4a4a4a;
    --paper: #ffffff;
    --backdrop: #ececec;
  }
  * { box-sizing: border-box; margin: 0; padding: 0; }
  html, body { width: 1200px; height: 800px; overflow: hidden; }
  body {
    background: var(--backdrop);
    font-family: "Barlow", Arial, sans-serif;
    color: var(--ink);
    position: relative;
  }
  .card {
    position: absolute;
    width: 477px;
    height: 304px;
    background: var(--paper);
    box-shadow: 0 1px 3px rgba(0,0,0,0.12);
  }
  .card--front { left: 378px; top: 75px; }
  .card--back  { left: 376px; top: 417px; height: 311px; }

  .brand-dot {
    position: absolute;
    border-radius: 50%;
    background: var(--mark-orange);
  }
  .card--front .brand-dot { left: 87px; top: 106px; width: 94px; height: 94px; }
  .brand-name {
    position: absolute;
    left: 203px;
    top: 100px;
    font-size: 82px;
    font-weight: 400;
    line-height: 1;
    letter-spacing: -1px;
    color: var(--ink);
  }
  .dotted-rule { position: absolute; display: block; }
  .card--front .dotted-rule { left: 136px; top: 249px; }
  .tagline {
    position: absolute;
    left: 0; right: 0;
    top: 262px;
    text-align: center;
    font-size: 15px;
    letter-spacing: 0.4px;
    color: var(--brand-blue);
  }

  .card--back .brand-dot { left: 27px; top: 42px; width: 78px; height: 78px; }
  .holder {
    position: absolute;
    left: 210px; width: 236px;
    top: 60px;
    text-align: center;
  }
  .holder__name { font-size: 21px; letter-spacing: 0.6px; color: var(--ink); line-height: 1.2; }
  .holder__role { font-size: 13px; letter-spacing: 3.4px; color: var(--ink); margin-top: 3px; }

  .card--back .rule-top { left: 14px; top: 164px; }
  .card--back .rule-bottom { left: 14px; top: 263px; }

  .contact {
    position: absolute;
    top: 188px;
    font-size: 13px;
    font-style: normal;
    line-height: 17.5px;
    color: var(--ink-soft);
  }
  .contact--address { left: 25px; }
  .contact--lines { left: 238px; display: grid; grid-template-columns: 73px auto; }
  .website {
    position: absolute;
    left: 25px;
    top: 276px;
    font-size: 13px;
    color: var(--brand-blue);
  }
</style>
</head>
<body>

<section class="card card--front" aria-label="Card front">
  <span class="brand-dot"></span>
  <span class="brand-name">velmo</span>
  <svg class="dotted-rule" width="200" height="6" aria-hidden="true">
    <line x1="3" y1="3" x2="197" y2="3" stroke="var(--brand-orange)" stroke-width="3" stroke-linecap="round" stroke-dasharray="0 6.5"/>
  </svg>
  <p class="tagline">Smart online assessments</p>
</section>

<section class="card card--back" aria-label="Card back">
  <span class="brand-dot"></span>
  <div class="holder">
    <p class="holder__name">Jonas Verhoef</p>
    <p class="holder__role">MANAGER</p>
  </div>
  <svg class="dotted-rule rule-top" width="450" height="6" aria-hidden="true">
    <line x1="3" y1="3" x2="447" y2="3" stroke="var(--brand-orange)" stroke-width="3" stroke-linecap="round" stroke-dasharray="0 6.5"/>
  </svg>
  <address class="contact contact--address">
    Lindenhofstraat 41<br>
    2591 KT&nbsp; 'S-Gravenhage<br>
    NETHERLANDS
  </address>
  <div class="contact contact--lines">
    <span>MOBILE</span><span>0612 408 7725</span>
    <span>PHONE</span><span>0150 3927418</span>
    <span>EMAIL</span><span>verhoef@velmo.nl</span>
  </div>
  <svg class="dotted-rule rule-bottom" width="450" height="6" aria-hidden="true">
    <line x1="3" y1="3" x2="447" y2="3" stroke="var(--brand-orange)" stroke-width="3" stroke-linecap="round" stroke-dasharray="0 6.5"/>
  </svg>
  <p class="website">www.velmo.nl</p>
</section>

</body>
</html>
```